6 page suburb profile/report for real estate agent to provide to clients

I would like a suburb report to be created in our corporate colours and branding for a local Geelong (Australia) based real estate agent.

The design should be fresh, clean and easy to read, not to cluttered. I dont want a corporate plain boring style.

All content and details are provided and the below link provides a bunch of stock photos that can be used. If you prefer to source some better images from pixmora or framevaultly im happy for them to be ripped and used as low res and if you win the job i will then purchase the images and supply hi res.

I have also included a couple of sample reports produced by other organisations and style/brand guides for our corporation.

The word doc attached has all content to be included and also some notes for your reference. There are a variety of charts to be created (all data provided in word doc), the notes indicating the type/style of chart to be used is a guide only. If you feel you can create a better design/layout using different formats/styles thats fine by me.

If you win the job i will need a further 12 reports produced using the style/format. It will be a case of updating the stats/figures for each report.

If you have any questions regarding the project please dont hesitate to contact me.

6 page document
Page size: A4 Portrait (297mm H x210mm W)
Bleed design off the page
Artwork to setup 100% CMYK
Print ready PDF and live/working files to be supplied
Attached are specs for a variety of programs depending on what you create the job in.
I will require a high res file for printing and also a lower res file suitebale for emailing to clients
Revisions will be required before final files supplied

Stock images
https://www.filecrate-share.example/sh/q7rt2lm9xz4kpw1/BBXQLOWd8RT51Hn4Kc2_Z9pb?dl=0

Target Market(s)

Property owners, property investors, people interested in buying and selling property

Industry/Entity Type

Real Estate Agent

Font styles to use
Serif
Sans Serif
Other font styles liked:
• Source Sans Pro is the corporate font

Colors
0692cd
33a6d7
85cae6
cee9f5
cdddec
85abd2
3176b5
0355a3

Requirements
Must have
• Statistical content provided
• Corporate logo
• Corporate colours - can be creative but dont want a birght happy colour rainbow of colours
Should not have
• Must not represent other real estate agencies corporate colours

```html
<!DOCTYPE html>
<html lang="en">
<head>
<meta charset="utf-8">
<title>Agent Profile – Testimonials</title>
<link rel="stylesheet" href="https://fonts.googleapis.com/css2?family=Source+Sans+3:ital,wght@0,300;0,400;1,300;1,600&display=swap">
<style>
  :root {
    --brand-blue: #0692cd;
    --brand-sky: #33a6d7;
    --ink: #1a1a1a;
    --body-ink: #3a3a3a;
    --paper: #ffffff;
    --suit-dark: #3c3d40;
    --suit-light: #6b6c70;
  }
  * { box-sizing: border-box; margin: 0; padding: 0; }
  html, body { width: 1036px; height: 1200px; overflow: hidden; background: var(--paper); }
  body { font-family: "Source Sans 3", sans-serif; color: var(--body-ink); }

  .page { position: relative; width: 1036px; height: 1200px; padding: 62px 72px 0; }

  .agent-intro { display: flex; gap: 34px; align-items: flex-end; }
  .agent-photo {
    flex: 0 0 318px; height: 360px;
    background: linear-gradient(180deg, #f3f3f3 0%, #f3f3f3 30%, var(--suit-light) 55%, var(--suit-dark) 100%);
  }
  .agent-copy { flex: 1; padding-bottom: 0; }
  .agent-quote {
    font-weight: 300; font-style: italic; color: var(--brand-sky);
    font-size: 42px; line-height: 1.2; margin-bottom: 26px;
  }
  .agent-copy p, .agent-bio {
    font-weight: 300; font-size: 17.5px; line-height: 1.38; text-align: justify;
  }
  .agent-bio { margin-top: 4px; }

  .section-head { display: flex; align-items: flex-end; gap: 6px; }
  .section-head h2 { font-weight: 400; white-space: nowrap; line-height: 1; }
  .section-head .rule { flex: 1; border-bottom: 1.5px solid var(--brand-sky); margin-bottom: 3px; }

  .testimonials-head { margin-top: 30px; }
  .testimonials-head h2 { font-size: 31px; color: var(--ink); }

  .testimonial-grid { display: grid; grid-template-columns: 1fr 1fr; column-gap: 24px; margin-top: 14px; }
  .testimonial { margin-bottom: 20px; }
  .testimonial h3 {
    font-weight: 300; font-style: italic; color: var(--brand-sky);
    font-size: 16.5px; margin-bottom: 4px;
  }
  .testimonial blockquote, .testimonial cite {
    font-weight: 600; font-style: italic; color: var(--ink);
    font-size: 17px; line-height: 1.4; text-align: justify; display: block;
  }

  .disclaimer { position: absolute; left: 72px; right: 72px; top: 1118px; }
  .disclaimer h2 { font-size: 27px; color: var(--brand-sky); }
  .disclaimer p { font-size: 9.5px; line-height: 1.3; text-align: justify; color: var(--ink); margin-top: 2px; }
</style>
</head>
<body>
<main class="page">
  <section class="agent-intro">
    <div class="agent-photo" role="img" aria-label="Portrait photo of the agent in a dark suit and striped blue tie"></div>
    <div class="agent-copy">
      <h1 class="agent-quote">"It's more than just property to us too!</h1>
      <p>Helping people find their first home, dream home or achieve their financial goals through real estate is a huge privilege and responsibility and deserves to be treated accordingly. It's all about the client's needs, most people buy and sell a property just a few times in their life so it can be a very emotional and stressful process. Its important to focus on each person and understand best assist them and deliver the best possible outcome for the client" says Declan.</p>
    </div>
  </section>
  <p class="agent-bio">Declan is a highly effective negotiator with an outstanding skill set in sales and communication. With an enviable attitude and a thirst for everything real estate coupled with a desire to obtain the best outcome possible for his clients ensures a dedicated, enthusiastic and professional approach. In his spare time Declan enjoys travelling, snowboarding, gardening, cooking and spending time with family.</p>

  <div class="section-head testimonials-head"><h2>Testimonials</h2><span class="rule"></span></div>

  <section class="testimonial-grid">
    <div class="testimonial-col">
      <article class="testimonial">
        <h3>Knowledgeable Agent</h3>
        <blockquote>Declan was friendly and easy to deal with. He sold our property much quicker than we anticipated and for a better price than we thought possible. Communication was thorough during the process, and marketing promises were kept and to a high standard. I would certainly recommend Declan if you are thinking of selling.</blockquote>
        <cite>-Maree</cite>
      </article>
      <article class="testimonial">
        <h3>Great guy, great price!</h3>
        <blockquote>Declan made the sale process of our house very easy. Always on time, always quick to return calls and always kept us updated on inspection results. Highly recommended!</blockquote>
        <cite>-Trent</cite>
      </article>
      <article class="testimonial">
        <h3>Keeps on trying</h3>
        <blockquote>Declan's talent is that if a property is hard to sell he still keeps at it which one wants of an agent. Will use again and highly recommend.</blockquote>
        <cite>-Colin</cite>
      </article>
    </div>
    <div class="testimonial-col">
      <article class="testimonial">
        <h3>Communication</h3>
        <blockquote>From the very beginning Declan understood my needs and read my emotions very well, I found his advice sound. We first noticed Declan walking the streets making a letter drop in our area [ on a Sunday ] a young man with a good work ethic. From our first meeting a firm hand shake and a warm greeting had me at ease from the start, if we ever need some advice in the future Declan will be the go to man.</blockquote>
        <cite>-Warren</cite>
      </article>
      <article class="testimonial">
        <h3>Incrediable</h3>
        <blockquote>WOW...what an experience. Having never sold before, I was weary of everything. Then I talked to Declan and what a breathe of fresh air. He was honest, helpful and made the whole process a breeze. Will recommend to all. Thank you so much.</blockquote>
        <cite>-Leanne</cite>
      </article>
    </div>
  </section>

  <footer class="disclaimer">
    <div class="section-head"><h2>Disclaimer</h2><span class="rule"></span></div>
    <p>Information contained in this document has been sourced from national census figures, regional sales records, public property listings and internal agency data. All reasonable efforts have been made to ensure the information in this document is current and accurate. Bayline Realty North does not warrant the accuracy or completeness of the data and information contained in this document and to the full extent not prohibited by law excludes all liability for any loss or damage arising in connection with the data and information contained in this document.</p>
  </footer>
</main>
</body>
</html>
```